Nitrogen generation business website

Project Overview:
This project aims to create a sleek, user-friendly, and responsive WordPress template for Flo7K3, a provider of Nitrogen generation solutions. The site will serve as a primary touchpoint for customers and businesses looking to enquire about or purchase Flo7K3 products and services. The website should clearly communicate the benefits of working with Flo7K3 as a distributor, focusing on ease of access, expert consultation, and fast, reliable service.
Target Audience:
• Industrial companies seeking Nitrogen solutions.
• Engineers, facility managers, and purchasing teams in need of high-quality Nitrogen systems.
• Partners or businesses seeking to collaborate or purchase through a distributor.
Key Objectives:
1. Establish Flo7K3’s Brand Identity: Use the bold, energetic logo and branding of Flo7K3 (as seen in the uploaded logo) throughout the design. Ensure the brand’s personality shines, with a focus on modernity, reliability, and innovation.
2. Showcase Products and Solutions: Display detailed product categories and descriptions, emphasising the solutions Flo7K3 offers.
3. Lead Generation: Incorporate contact forms, quote requests, and easy-to-find CTAs to convert visitors into leads.
4. User-Centric Design: The design must be intuitive and user-friendly, providing a smooth experience across desktop and mobile devices.
Design Requirements:
1. Home Page:
• Hero Banner: A dynamic, visually engaging hero banner featuring air and gas purification systems, paired with strong CTAs like “Request a Quote” or “Contact Us for Solutions.” The banner should align with the vibrant red and yellow tones in the Flo7K3 logo.
• Key Product Categories: Introduce the main product categories with icons or images linked to individual product pages.
• Flo7K3 Expertise Section: A section emphasising the company’s role as a trusted distributor, backed by experience and a strong partnership network.
• Why Choose Flo7K3: Highlight 3-4 major benefits, such as “Quick Delivery,” “Expert Consultation,” and “Innovative Technology.”
• Client Testimonials/Partners: Space for customer feedback, testimonials, or logos of partner companies to build trust.
• Newsletter or Enquiry Form: Place a compact form for capturing visitor details for quotes, enquiries, or subscriptions.
2. Product Pages:
• Category Pages: Create well-structured product category pages (e.g., Air Filtration Systems, Nitrogen Generators) similar to industry-standard designs. Each category page should feature professional imagery, short product descriptions, and links to detail pages.
• Product Detail Pages: Each product page will contain:
• High-quality images of the product.
• Detailed specifications, technical descriptions, and features.
• Options to download datasheets or brochures (PDF format).
• Clear CTAs to request a quote or contact sales.
• Product Comparison Tool (Optional): Allow users to compare multiple products, emphasising key features and specifications.
3. About Flo7K3 Page:
• Provide an overview of Flo7K3’s history, mission, and the value it provides as a leading distributor.
• Highlight industry expertise, the partnership network, and any accolades or certifications.
• Mention any regional advantages or special services (e.g., fast delivery times, on-site consultation).
4. Contact Us Page:
• Clean and Simple Form: Include fields for general inquiries or specific product requests.
• Contact Information: Display the company’s, email address info@flo7k3.co.uk.
5. Additional Functionalities:
• Responsive Design: Ensure the design is fully responsive, optimised for mobile, tablet, and desktop viewing.
• SEO Optimisation: Include best practices for search engine optimization (SEO), including clean URLs, meta tags, and image alt text.
• Fast Loading Speed: Optimise images, scripts, and code for fast loading times to improve user experience.
• Social Media Integration: Provide links to social media profiles (if applicable) and potentially include a feed for recent updates.
• Optional Blog: Create a blog space for sharing industry news, product updates, or educational content to engage with visitors and improve SEO.
Style Guide:
1. Color Palette:
• Use colors consistent with the Flo7K3 logo: Red (#FF0000) and Yellow (#FFD700) as primary colors. Incorporate neutral colors (such as white, gray, or black) for balance and readability.
• Accent colors may be introduced for subtle highlights, but the focus should be on the bold, energetic color scheme of Flo7K3.
2. Typography:
• Primary Font for Headings: A bold, modern sans-serif font that complements the strong branding of Flo7K3.
• Secondary Font for Body Text: Clean, easy-to-read sans-serif or serif font for optimal readability across devices.
• Typography Emphasis: Use large, bold typography for headlines to match the boldness of the logo and brand identity.
3. Imagery:
• Use high-quality industrial and technical imagery that reflects the air and gas purification products Flo7K3 distributes.
• Incorporate imagery showing products in action, e.g., in industrial settings or installations.
• Avoid clutter; ensure images are used to enhance user understanding, not overwhelm.
4. Icons:
• Utilise modern, flat-style icons that align with the clean and professional image of Flo7K3. Icons could represent services such as “Fast Delivery,” “Expert Support,” and “High-Quality Products.”
Functionality Requirements:
1. Content Management System (CMS): Build the site using WordPress for easy content management, allowing Flo7K3 staff to update content, product information, and blog posts.
2. Quote Request Integration: Ensure the site has a functional and easy-to-access “Request a Quote” form that appears on every product and service page.
3. Customer Support Section: Optionally include a section for FAQs, product guides, or a knowledge base to support customers and prospects.
4. Security: Implement SSL encryption and ensure that other security best practices (e.g., spam prevention for forms) are followed.
5. Multilingual Support (Optional): Provide the option to support multiple languages, depending on the regional scope of Flo7K3’s distribution services.
Deliverables:
• WordPress template with a homepage, product pages, about section, and contact page.
• SEO-friendly and responsive design.
• Clear CTAs for lead generation (e.g., “Request a Quote”).
• User-friendly interface for both desktop and mobile devices.
Inspiration/Competitors:
• Competitor Analysis: Research similar distributors in the air and gas purification industry for design inspiration.
• Brand Consistency: Ensure Flo7K3’s bold branding is prominent and differentiates it from competitors.
Target Market(s)
Food & Beverage manufacturers, Laser Cutting, Electronics manufacturers, General Industrial Manufacturers

```html
<!DOCTYPE html>
<html lang="en">
<head>
<meta charset="utf-8">
<title>Flo7K3 — Website Home Page, Desktop and Mobile</title>
<link rel="stylesheet" href="https://fonts.googleapis.com/css2?family=Lexend:wght@300;400;500;600;700&display=swap">
<style>
:root{
  --board:#3a3d3a;
  --paper:#dfe4e3;
  --yellow:#ffb800;
  --red:#ff1200;
  --ink:#1b1b1b;
  --white:#ffffff;
}
*{box-sizing:border-box;margin:0;padding:0}
html,body{width:1200px;height:1200px;overflow:hidden;background:var(--board)}
body{font-family:"Lexend",sans-serif;color:var(--ink)}
.board{position:absolute;left:0;top:0;width:1932px;height:1932px;transform:scale(.62112);transform-origin:0 0;background:var(--board)}
.abs{position:absolute}
.board-label{position:absolute;top:52px;font-size:14px;color:#e8e8e8;font-weight:300}
.frame{position:absolute;background:var(--paper);overflow:hidden}
.desktop{left:542px;top:79px;width:540px;height:1811px}
.mobile{left:1144px;top:81px;width:246px;height:1805px}
.brand{position:absolute;font-weight:700;color:var(--red);letter-spacing:-.5px}
.nav{position:absolute;display:flex;gap:9px;font-size:4.2px;font-weight:600;letter-spacing:.2px}
.yellow{background:var(--yellow)}
.red{background:var(--red)}
.btn{position:absolute;background:var(--red);color:var(--white);font-weight:600;display:flex;align-items:center;justify-content:center;border-radius:3px;white-space:nowrap}
.photo{position:absolute;border-radius:6px}
.photo-worker{background:linear-gradient(135deg,#1f6c6a 0%,#2f4a48 35%,#d59a2c 55%,#3b3f3a 80%,#1d2b2a 100%)}
.photo-tablet{background:linear-gradient(160deg,#6c7378 0%,#48505a 35%,#e2b224 60%,#2f3133 100%)}
.product-area{position:absolute;background:linear-gradient(180deg,rgba(225,228,230,.55),rgba(150,155,160,.55));border-radius:4px}
.headline{white-space:nowrap}
.tile{position:absolute;width:66px;height:66px;border-radius:6px;display:flex;align-items:center;justify-content:center}
.tile-label{position:absolute;text-align:center;font-weight:300;line-height:1.2}
.checks{position:absolute;display:grid;grid-template-columns:1fr 1fr;column-gap:8px}
.check{display:flex;gap:5px;align-items:flex-start;font-weight:300;line-height:1.25}
.check svg{flex:none;margin-top:1px}
.why-card{position:absolute;border-radius:6px;padding:14px 15px}
.why-icon{width:38px;height:38px;border-radius:3px;display:flex;align-items:center;justify-content:center;margin-bottom:16px}
.why-card h4{font-size:8.6px;font-weight:600;line-height:1.25;margin-bottom:8px}
.why-card p{font-size:3.6px;line-height:1.45;font-weight:300}
.quote-mark{position:absolute;color:var(--yellow);font-weight:700;text-align:center}
.avatar{position:absolute;border-radius:50%;border:2px solid var(--white)}
.field{position:absolute;background:#eef0ef;border-radius:16px;color:#a2a6a5;display:flex;align-items:center;font-weight:300}
.field .btn{top:0;right:0;height:100%;border-radius:16px}
.foot-col{position:absolute;font-size:4.2px;font-weight:300;line-height:1.5}
.foot-col h5{font-size:8px;font-weight:600;margin-bottom:14px}
.social{position:absolute;width:14px;height:14px;border-radius:50%;background:var(--red)}
</style>
</head>
<body>
<div class="board">
  <div class="board-label" style="left:542px">Dekstop</div>
  <div class="board-label" style="left:1144px">Mobile</div>

  <!-- DESKTOP -->
  <div class="frame desktop">
    <header>
      <div class="brand" style="left:56px;top:16px;font-size:20px">Flo7K3</div>
      <nav class="nav" style="left:216px;top:26px">
        <span>HOME</span><span>PRODUCT</span><span>ABOUT US</span><span>SERVICES</span><span>BLOG</span><span>CONTACT US</span>
      </nav>
      <svg class="abs" style="left:438px;top:23px" width="52" height="10" viewBox="0 0 52 10" fill="none" stroke="#222" stroke-width=".8">
        <circle cx="4" cy="3" r="2"/><path d="M1 9c0-2 1.5-3 3-3s3 1 3 3"/>
        <rect x="20" y="2" width="7" height="7" rx="1"/><path d="M22 2c0-1.5 3-1.5 3 0"/>
        <text x="38" y="6.5" font-size="3.5" fill="#444" stroke="none" font-family="Lexend">GBP</text>
      </svg>
    </header>

    <section class="yellow abs" style="left:0;top:52px;width:540px;height:286px;border-bottom-left-radius:60px">
      <h1 class="abs headline" style="left:56px;top:18px;font-size:26px;font-weight:500;line-height:31px">Enhance Your Operations<br>with Reliable Nitrogen Solutions</h1>
      <p class="abs" style="left:56px;top:120px;font-size:8px;font-weight:300;line-height:1.3;width:180px">Discover How Our Advanced Nitrogen Generators Can Optimise Your Business</p>
      <a class="btn" style="left:56px;top:187px;width:102px;height:30px;font-size:8px">Request a Quote</a>
      <svg class="abs" style="left:56px;top:259px" width="30" height="6"><circle cx="3" cy="3" r="2.4" fill="#ff1200"/><circle cx="13" cy="3" r="2.2" fill="none" stroke="#ff1200" stroke-width=".7"/><circle cx="23" cy="3" r="2.2" fill="none" stroke="#ff1200" stroke-width=".7"/></svg>
      <div class="red abs" style="left:251px;top:87px;width:192px;height:199px;border-radius:96px 96px 0 0/88px 60px 0 0"></div>
      <div class="product-area" role="img" aria-label="Product photo of two nitrogen generator units" style="left:334px;top:92px;width:130px;height:190px"></div>
    </section>

    <section>
      <h2 class="abs" style="left:56px;top:377px;font-size:17.5px;font-weight:600;line-height:21px">Explore Our<br>Solutions</h2>
      <p class="abs" style="left:56px;top:435px;font-size:8px;font-weight:300;line-height:1.3;width:150px">Find the Right Nitrogen Generator for Your Needs</p>
      <div class="tile red" style="left:270px;top:377px"><svg width="36" height="38" viewBox="0 0 36 38" fill="none" stroke="#ffb800" stroke-width="1.4"><rect x="8" y="4" width="20" height="28" rx="2"/><rect x="12" y="9" width="12" height="8"/><circle cx="18" cy="23" r="3"/><path d="M4 34h28M12 2v2M24 2v2"/></svg></div>
      <div class="tile yellow" style="left:344px;top:377px"><svg width="34" height="38" viewBox="0 0 34 38" fill="none" stroke="#ff1200" stroke-width="1.4"><path d="M6 4h8v4l-1 4v18a3 3 0 0 1-6 0V12L6 8zM20 4h8v4l-1 4v18a3 3 0 0 1-6 0V12l-1-4z"/><path d="M14 6h6"/></svg></div>
      <div class="tile red" style="left:417px;top:377px"><svg width="34" height="38" viewBox="0 0 34 38" fill="none" stroke="#ffb800" stroke-width="1.4"><rect x="5" y="11" width="24" height="24" rx="2"/><path d="M9 11V6h16v5M13 6V2h8v4M5 18h24"/></svg></div>
      <p class="tile-label" style="left:262px;top:457px;width:82px;font-size:8.5px">Nitrogen<br>Generators</p>
      <p class="tile-label" style="left:336px;top:457px;width:82px;font-size:8.5px">Filtration<br>Systems</p>
      <p class="tile-label" style="left:404px;top:457px;width:92px;font-size:8.5px">Air Purification<br>Solutions</p>
    </section>

    <section>
      <div class="photo photo-worker" role="img" aria-label="Engineer in a yellow hard hat working on plant pipework" style="left:56px;top:507px;width:174px;height:235px"></div>
      <div class="yellow abs" style="left:237px;top:507px;width:247px;height:235px;border-radius:8px">
        <h2 class="abs" style="left:28px;top:23px;font-size:17px;font-weight:600;line-height:21px;width:200px">Our Expertise in Advanced Nitrogen Technology</h2>
        <div class="checks" style="left:29px;top:103px;width:200px;row-gap:14px;font-size:8px">
          <div class="check"><svg width="9" height="9" viewBox="0 0 9 9" fill="none" stroke="#ff1200" stroke-width=".9"><rect x=".5" y=".5" width="8" height="8" rx="2"/><path d="M2.5 4.6l1.5 1.5 2.6-3"/></svg><span>Comprehensive<br>Solutions</span></div>
          <div class="check"><svg width="9" height="9" viewBox="0 0 9 9" fill="none" stroke="#ff1200" stroke-width=".9"><rect x=".5" y=".5" width="8" height="8" rx="2"/><path d="M2.5 4.6l1.5 1.5 2.6-3"/></svg><span>Experienced Team</span></div>
          <div class="check"><svg width="9" height="9" viewBox="0 0 9 9" fill="none" stroke="#ff1200" stroke-width=".9"><rect x=".5" y=".5" width="8" height="8" rx="2"/><path d="M2.5 4.6l1.5 1.5 2.6-3"/></svg><span>Advanced<br>Technology</span></div>
          <div class="check"><svg width="9" height="9" viewBox="0 0 9 9" fill="none" stroke="#ff1200" stroke-width=".9"><rect x=".5" y=".5" width="8" height="8" rx="2"/><path d="M2.5 4.6l1.5 1.5 2.6-3"/></svg><span>Global<br>Partnerships</span></div>
        </div>
        <a class="btn" style="left:30px;top:178px;width:102px;height:30px;font-size:8px">Contact Us</a>
      </div>
    </section>

    <section>
      <h2 class="abs" style="left:0;top:778px;width:540px;text-align:center;font-size:17px;font-weight:600">Why Choose Flo7K3</h2>
      <div class="why-card red" style="left:56px;top:822px;width:139px;height:130px;color:var(--white)">
        <div class="why-icon yellow"><svg width="22" height="16" viewBox="0 0 22 16" fill="none" stroke="#ff1200" stroke-width="1"><path d="M1 2h12v11H1zM13 6h4l4 4v3h-8z"/><circle cx="5" cy="14" r="1.5"/><circle cx="17" cy="14" r="1.5"/></svg></div>
        <h4>Fast and Flexible<br>Delivery</h4>
        <p style="color:#ffb3a8">Streamlined processes mean quick delivery and flexible install slots that fit your project timelines.</p>
      </div>
      <div class="why-card yellow" style="left:201px;top:831px;width:138px;height:130px">
        <div class="why-icon red"><svg width="22" height="18" viewBox="0 0 22 18" fill="none" stroke="#ffb800" stroke-width="1"><rect x="1" y="4" width="11" height="9" rx="1"/><rect x="9" y="1" width="12" height="9" rx="1"/><path d="M12 4h6M12 6.5h6"/></svg></div>
        <h4>Expert Consultation<br>and Support</h4>
        <p>Our team of experts offers tailored advice and ongoing support to help you choose and maintain the right system.</p>
      </div>
      <div class="why-card yellow" style="left:346px;top:831px;width:138px;height:130px">
        <div class="why-icon red"><svg width="22" height="20" viewBox="0 0 22 20" fill="none" stroke="#ffb800" stroke-width="1"><path d="M7 9h8l-2 6H9zM9 17h4M11 1v3M3 4l2 2M19 4l-2 2"/></svg></div>
        <h4>Innovative<br>Technology</h4>
        <p>We stay ahead of industry trends, building the latest technology into our products so you get modern solutions.</p>
      </div>
    </section>

    <section class="red abs" style="left:0;top:1002px;width:540px;height:287px;border-bottom-right-radius:60px;color:var(--white)">
      <h2 class="abs" style="left:0;top:34px;width:540px;text-align:center;font-size:16.5px;font-weight:600">What Our Clients Say</h2>
      <div class="quote-mark" style="left:0;top:60px;width:540px;font-size:48px;line-height:1">“</div>
      <p class="abs" style="left:54px;top:116px;width:432px;text-align:center;font-size:8.4px;font-weight:300;line-height:1.3">We've worked with Flo7K3 for several years and have always been impressed by their professionalism and expertise. Their solutions are top-notch, and their quick delivery has been crucial for our tight schedules.</p>
      <p class="abs" style="left:0;top:163px;width:540px;text-align:center;font-size:8.2px;font-weight:600">Mara Ellison, Plant Manager, Norvale Industrial</p>
      <div class="avatar" role="img" aria-label="Client portrait" style="left:159px;top:206px;width:42px;height:42px;background:linear-gradient(135deg,#6fb7a0,#d9a27a)"></div>
      <div class="avatar" role="img" aria-label="Client portrait" style="left:219px;top:206px;width:42px;height:42px;background:linear-gradient(135deg,#f3efe8,#b68b6a)"></div>
      <div class="avatar" role="img" aria-label="Client portrait" style="left:279px;top:206px;width:42px;height:42px;background:linear-gradient(135deg,#5aa6d8,#e0b592)"></div>
      <div class="avatar" role="img" aria-label="Client portrait" style="left:339px;top:206px;width:42px;height:42px;border-color:var(--red);background:linear-gradient(135deg,#2f2b2b,#8a5a44)"></div>
    </section>

    <section>
      <div class="yellow abs" style="left:56px;top:1329px;width:247px;height:234px;border-radius:6px">
        <h2 class="abs" style="left:27px;top:32px;font-size:16.5px;font-weight:600;line-height:21px">Stay Updated with<br>Flo7K3</h2>
        <p class="abs" style="left:26px;top:108px;width:190px;font-size:8.3px;font-weight:300;line-height:1.3">Join our mailing list to receive updates on new products, industry news, and exclusive offers.</p>
        <div class="field" style="left:27px;top:165px;width:182px;height:31px;font-size:8px;padding-left:20px">Enter your email<a class="btn" style="width:68px;font-size:8px">Subscribe</a></div>
      </div>
      <div class="photo photo-tablet" role="img" aria-label="Smiling engineer in hard hat and hi-vis vest holding a tablet" style="left:310px;top:1326px;width:174px;height:235px"></div>
    </section>

    <footer class="yellow abs" style="left:0;top:1609px;width:540px;height:202px;border-top-left-radius:60px">
      <div class="brand" style="left:56px;top:44px;font-size:20px">Flo7K3</div>
      <p class="foot-col" style="left:56px;top:86px;width:78px">You minim mollit non deserunt ullamco est sit aliqua dolor do amet sint. Velit officia consequat duis.</p>
      <div class="foot-col" style="left:180px;top:56px;width:90px">
        <h5>Get In Touch</h5>
        <div style="display:flex;gap:10px;margin-bottom:8px"><svg width="9" height="10" viewBox="0 0 9 10" fill="none" stroke="#ff1200" stroke-width=".8"><path d="M4.5 9.5S1 6 1 4a3.5 3.5 0 0 1 7 0c0 2-3.5 5.5-3.5 5.5z"/><circle cx="4.5" cy="4" r="1"/></svg><span>2280 Harlow Ave. Kestrel, Ohio 40120</span></div>
        <div style="display:flex;gap:10px;margin-bottom:8px"><svg width="9" height="8" viewBox="0 0 9 8" fill="none" stroke="#ff1200" stroke-width=".8"><rect x=".5" y=".5" width="8" height="7" rx="1"/><path d="M.5 1.5l4 3 4-3"/></svg><span>support@flo7k3.co.uk<br>info@flo7k3.co.uk</span></div>
        <div style="display:flex;gap:10px"><svg width="9" height="9" viewBox="0 0 9 9" fill="none" stroke="#ff1200" stroke-width=".8"><path d="M1 1.5l2-1 1.5 2.5-1 1a5 5 0 0 0 2 2l1-1L9 6.5l-1 2C4 8.5.5 5 1 1.5z"/></svg><span>(310) 555-0142<br>(310) 555-0187</span></div>
      </div>
      <div class="foot-col" style="left:288px;top:56px;width:70px">
        <h5>Explore Link</h5>
        <div style="line-height:4.1;margin-top:-8px">About Us<br>Career<br>FAQ<br>Blog<br>Product</div>
      </div>
      <div class="foot-col" style="left:384px;top:56px;width:100px">
        <h5>Office Time</h5>
        <p>Mon-Sat: 10.00AM – 4.00PM<br>Sunday: 10.00AM – 4.00PM<br>Friday: Close</p>
      </div>
      <div class="social" style="left:385px;top:126px"></div>
      <div class="social" style="left:411px;top:126px"></div>
      <div class="social" style="left:437px;top:126px"></div>
    </footer>
  </div>

  <!-- MOBILE -->
  <div class="frame mobile">
    <header>
      <div class="brand" style="left:18px;top:12px;font-size:14px">Flo7K3</div>
      <svg class="abs" style="left:208px;top:14px" width="22" height="14" viewBox="0 0 22 14" stroke="#ff1200" stroke-width="1.3"><path d="M0 1h22M0 7h22M0 13h22"/></svg>
    </header>

    <section class="yellow abs" style="left:0;top:40px;width:246px;height:394px;border-bottom-left-radius:50px">
      <h1 class="abs headline" style="left:17px;top:15px;font-size:19.5px;font-weight:500;line-height:25.5px">Enhance Your<br>Operations<br>with Reliable<br>Nitrogen Solutions</h1>
      <p class="abs" style="left:17px;top:137px;width:150px;font-size:6.5px;font-weight:300;line-height:1.35">Discover How Our Advanced Nitrogen Generators Can Optimise Your Business</p>
      <a class="btn" style="left:18px;top:180px;width:83px;height:25px;font-size:6.5px">Request a Quote</a>
      <div class="red abs" style="left:50px;top:233px;width:196px;height:161px;border-radius:80px 0 0 0/80px 0 0 0"></div>
      <div class="product-area" role="img" aria-label="Product photo of two nitrogen generator units" style="left:120px;top:238px;width:102px;height:154px"></div>
    </section>

    <section>
      <h2 class="abs" style="left:19px;top:470px;font-size:14px;font-weight:600">Explore Our Solutions</h2>
      <p class="abs" style="left:18px;top:499px;font-size:6.5px;font-weight:300">Find the Right Nitrogen Generator for Your Needs</p>
      <div class="tile red" style="left:18px;top:531px"><svg width="36" height="38" viewBox="0 0 36 38" fill="none" stroke="#ffb800" stroke-width="1.4"><rect x="8" y="4" width="20" height="28" rx="2"/><rect x="12" y="9" width="12" height="8"/><circle cx="18" cy="23" r="3"/><path d="M4 34h28M12 2v2M24 2v2"/></svg></div>
      <div class="tile yellow" style="left:91px;top:531px"><svg width="34" height="38" viewBox="0 0 34 38" fill="none" stroke="#ff1200" stroke-width="1.4"><path d="M6 4h8v4l-1 4v18a3 3 0 0 1-6 0V12L6 8zM20 4h8v4l-1 4v18a3 3 0 0 1-6 0V12l-1-4z"/><path d="M14 6h6"/></svg></div>
      <div class="tile red" style="left:163px;top:531px"><svg width="34" height="38" viewBox="0 0 34 38" fill="none" stroke="#ffb800" stroke-width="1.4"><rect x="5" y="11" width="24" height="24" rx="2"/><path d="M9 11V6h16v5M13 6V2h8v4M5 18h24"/></svg></div>
      <p class="tile-label" style="left:11px;top:610px;width:80px;font-size:6.5px">Nitrogen<br>Generators</p>
      <p class="tile-label" style="left:84px;top:610px;width:80px;font-size:6.5px">Filtration Systems</p>
      <p class="tile-label" style="left:156px;top:610px;width:80px;font-size:6.5px">Air Purification<br>Solutions</p>
    </section>

    <div class="photo photo-worker" role="img" aria-label="Engineer in a yellow hard hat working on plant pipework" style="left:18px;top:649px;width:210px;height:195px"></div>

    <section class="yellow abs" style="left:18px;top:861px;width:210px;height:200px;border-radius:4px">
      <h2 class="abs" style="left:23px;top:20px;width:170px;font-size:13.5px;font-weight:600;line-height:17px">Our Expertise in Advanced Nitrogen Technology</h2>
      <div class="checks" style="left:24px;top:88px;width:172px;row-gap:12px;font-size:6.2px">
        <div class="check"><svg width="8" height="8" viewBox="0 0 9 9" fill="none" stroke="#ff1200" stroke-width=".9"><rect x=".5" y=".5" width="8" height="8" rx="2"/><path d="M2.5 4.6l1.5 1.5 2.6-3"/></svg><span>Comprehensive<br>Solutions</span></div>
        <div class="check"><svg width="8" height="8" viewBox="0 0 9 9" fill="none" stroke="#ff1200" stroke-width=".9"><rect x=".5" y=".5" width="8" height="8" rx="2"/><path d="M2.5 4.6l1.5 1.5 2.6-3"/></svg><span>Experienced Team</span></div>
        <div class="check"><svg width="8" height="8" viewBox="0 0 9 9" fill="none" stroke="#ff1200" stroke-width=".9"><rect x=".5" y=".5" width="8" height="8" rx="2"/><path d="M2.5 4.6l1.5 1.5 2.6-3"/></svg><span>Advanced<br>Technology</span></div>
        <div class="check"><svg width="8" height="8" viewBox="0 0 9 9" fill="none" stroke="#ff1200" stroke-width=".9"><rect x=".5" y=".5" width="8" height="8" rx="2"/><path d="M2.5 4.6l1.5 1.5 2.6-3"/></svg><span>Global Partnerships</span></div>
      </div>
      <a class="btn" style="left:25px;top:152px;width:87px;height:26px;font-size:6.5px">Contact Us</a>
    </section>

    <section class="red abs" style="left:0;top:1077px;width:246px;height:270px;border-bottom-right-radius:50px;color:var(--white)">
      <h2 class="abs" style="left:0;top:28px;width:246px;text-align:center;font-size:13px;font-weight:600;line-height:17px">What Our<br>Clients Say</h2>
      <div class="quote-mark" style="left:0;top:64px;width:246px;font-size:36px;line-height:1">“</div>
      <p class="abs" style="left:18px;top:114px;width:210px;text-align:center;font-size:6.4px;font-weight:300;line-height:1.35">We've worked with Flo7K3 for several years and have always been impressed by their professionalism and expertise. Their solutions are top-notch, and their quick delivery has been crucial for our tight schedules.</p>
      <p class="abs" style="left:0;top:176px;width:246px;text-align:center;font-size:6.5px;font-weight:600">Mara Ellison, Plant Manager, Norvale Industrial</p>
      <div class="avatar" role="img" aria-label="Client portrait" style="left:104px;top:207px;width:38px;height:38px;background:linear-gradient(135deg,#f3efe8,#b68b6a)"></div>
    </section>

    <div class="photo photo-tablet" role="img" aria-label="Smiling engineer in hard hat and hi-vis vest holding a tablet" style="left:18px;top:1363px;width:210px;height:195px"></div>

    <section class="yellow abs" style="left:16px;top:1573px;width:214px;height:203px;border-radius:4px">
      <h2 class="abs" style="left:24px;top:27px;font-size:13px;font-weight:600;line-height:17px">Stay Updated with<br>Flo7K3</h2>
      <p class="abs" style="left:23px;top:94px;width:175px;font-size:6.4px;font-weight:300;line-height:1.35">Join our mailing list to receive updates on new products, industry news, and exclusive offers.</p>
      <div class="field" style="left:24px;top:143px;width:157px;height:27px;font-size:6.4px;padding-left:17px">Enter your email<a class="btn" style="width:60px;font-size:6.4px">Subscribe</a></div>
    </section>
  </div>
</div>
</body>
</html>
```